Marigold hair home studio

MARIGOLD HAIR.....at fox valley ,Wahroonga is a home hairdressing studio.
Hair services from a peaceful setting.
Quality colours and products.
free consultation prior to making appointment.
Easy and convenient after hours hair appointments.
Qualified hairdresser with over 15 years experience.
Specialise in foiling,balayage,ombre colour,tints,style cutting and blowdrying.
20 % off for new clients(colour services)
sms or call for 0412639074 for a quote.
im sorry guys but i has to re do alot of the photos. i would like something that looks elegant and classy.i will post an example of a flier style i like Added Wednesday, April 27, 2016
Project Deadline Extended Reason: im sorry i have decided i needed better photographs. please design again...i will choose someone before the deadline. please an elegant design will be great Added Wednesday, April 27, 2016
Target Market(s)
18-60 year olds
Industry/Entity Type
Hair
Requirements
Must have
- Must say home hairdressing studio
- Must say Marigold Hair at Fox Valley Wahroonga
- Must say phone number
Nice to have
- Modern but still classy and elegant
- Try to incorporate any photos which I have uploaded that looks best

```html
<!DOCTYPE html>
<html lang="en">
<head>
<meta charset="utf-8">
<title>Marigold Hair – Home Hairdressing Studio Flyer</title>
<link href="https://fonts.googleapis.com/css2?family=Cinzel:wght@500&family=Josefin+Sans:wght@700&family=Quicksand:wght@500;600&family=Lora:ital@1&family=Playfair+Display:wght@400&display=swap" rel="stylesheet">
<style>
  :root{
    --page:#ece7e0;
    --slate-top:#626264;
    --slate-bottom:#2a292b;
    --gold:#d9b27a;
    --gold-deep:#b8843e;
    --gold-light:#f3dcae;
    --amber:#e9963f;
    --cream:#ffffff;
    --pink:#e3157f;
    --ink:#1b1410;
  }
  *{margin:0;padding:0;box-sizing:border-box}
  html,body{width:1200px;height:1200px;overflow:hidden;background:var(--page)}
  .flyer{position:absolute;left:35px;top:201px;width:1130px;height:798px;overflow:hidden;
    background:linear-gradient(150deg,var(--slate-top) 0%,#404042 45%,var(--slate-bottom) 100%)}
  .flyer-art{position:absolute;inset:0;width:1130px;height:798px}
  .brand{position:absolute;left:35px;top:12px;width:370px;text-align:center;color:var(--gold);
    font-family:"Cinzel",serif;font-weight:500}
  .brand-name{font-size:72px;line-height:86px;letter-spacing:1px}
  .brand-sub{position:relative;font-size:54px;line-height:60px}
  .brand-sub::before,.brand-sub::after{content:"";position:absolute;top:31px;width:90px;height:2px;background:var(--gold)}
  .brand-sub::before{left:0}
  .brand-sub::after{right:0}
  .brand-studio{margin-top:6px;font-family:"Quicksand",sans-serif;font-weight:600;font-size:13px;line-height:18px;
    letter-spacing:3px;color:var(--cream)}
  .experience{position:absolute;left:80px;top:214px;display:flex;align-items:flex-end;gap:18px;color:var(--gold)}
  .experience-years{font-family:"Playfair Display",serif;font-size:72px;line-height:70px}
  .experience-label{font-family:"Quicksand",sans-serif;font-weight:600;font-size:16px;letter-spacing:5px;color:var(--cream);padding-bottom:14px}
  .services-title{position:absolute;left:52px;top:303px;font-family:"Josefin Sans",sans-serif;font-weight:700;
    font-size:33px;letter-spacing:4px;color:var(--gold)}
  .services{position:absolute;left:52px;top:350px;list-style:none}
  .services li{display:flex;align-items:center;gap:8px;height:33.5px;font-family:"Quicksand",sans-serif;font-weight:500;
    font-size:27px;letter-spacing:2.5px;color:var(--cream)}
  .services svg{width:20px;height:20px;flex:none}
  .tagline{position:absolute;font-family:"Lora",serif;font-style:italic;font-size:29px;letter-spacing:2px}
  .tagline-accent{left:55px;top:565px;color:var(--pink)}
  .tagline-rest{left:183px;top:598px;color:var(--cream)}
  .contact{position:absolute;left:253px;top:674px;color:var(--ink)}
  .contact-lead{font-family:"Quicksand",sans-serif;font-weight:500;font-size:19px;line-height:22px}
  .contact-number{font-family:"Playfair Display",serif;font-size:54px;line-height:56px;letter-spacing:1px}
</style>
</head>
<body>
<main class="flyer">
  <svg class="flyer-art" viewBox="0 0 1130 798">
    <defs>
      <linearGradient id="band-peach" x1="0" y1="0" x2="1" y2="1">
        <stop offset="0" stop-color="#f6d6b8"/><stop offset=".5" stop-color="#e8a66e"/><stop offset="1" stop-color="#f9e1c8"/>
      </linearGradient>
      <linearGradient id="hero-tones" x1="0" y1="0" x2="1" y2="0">
        <stop offset="0" stop-color="#e2cab6"/><stop offset=".3" stop-color="#b99279"/>
        <stop offset=".55" stop-color="#6b4430"/><stop offset=".8" stop-color="#3a2418"/><stop offset="1" stop-color="#241510"/>
      </linearGradient>
      <linearGradient id="ring-gold" x1="0" y1="0" x2="1" y2="1">
        <stop offset="0" stop-color="#e88a35"/><stop offset=".45" stop-color="#f8dba6"/><stop offset="1" stop-color="#c7772c"/>
      </linearGradient>
      <radialGradient id="tone-auburn"><stop offset="0" stop-color="#e7b294"/><stop offset="1" stop-color="#9a3a18"/></radialGradient>
      <radialGradient id="tone-brunette"><stop offset="0" stop-color="#ecd0bb"/><stop offset="1" stop-color="#7a4e35"/></radialGradient>
      <radialGradient id="tone-copper"><stop offset="0" stop-color="#e6b08e"/><stop offset="1" stop-color="#a9491f"/></radialGradient>
      <linearGradient id="pill-gold" x1="0" y1="0" x2="1" y2="0">
        <stop offset="0" stop-color="#e89a4a"/><stop offset=".5" stop-color="#f2d08c"/><stop offset="1" stop-color="#e6bf72"/>
      </linearGradient>
    </defs>

    <path d="M562 0 C440 180 430 520 760 798 L1130 798 L1130 0 Z" fill="url(#band-peach)"/>
    <path d="M580 0 C458 180 450 520 782 798 L1130 798 L1130 0 Z" fill="#fbeee2"/>
    <path d="M598 0 C476 180 470 520 806 798 L1130 798 L1130 0 Z" fill="url(#hero-tones)"
      role="img" aria-label="Photo of a woman with long glossy straight brunette hair and colourful feather earrings"/>

    <g class="portrait">
      <circle cx="520" cy="165" r="84" fill="url(#tone-auburn)" role="img" aria-label="Photo of a woman with long curly auburn hair"/>
      <circle cx="520" cy="165" r="84" fill="none" stroke="url(#ring-gold)" stroke-width="9"/>
    </g>
    <g class="portrait">
      <circle cx="497" cy="353" r="86" fill="url(#tone-brunette)" role="img" aria-label="Photo of a smiling woman with brown hair beside colour foil samples"/>
      <circle cx="497" cy="353" r="86" fill="none" stroke="url(#ring-gold)" stroke-width="9"/>
    </g>
    <g class="portrait">
      <circle cx="548" cy="562" r="86" fill="url(#tone-copper)" role="img" aria-label="Photo of a woman with a sleek copper bob haircut"/>
      <circle cx="548" cy="562" r="86" fill="none" stroke="url(#ring-gold)" stroke-width="9"/>
    </g>

    <g class="call-badge">
      <path d="M120 712 C160 716 175 690 215 670 L215 766 C175 752 160 760 120 758 Z" fill="url(#pill-gold)"/>
      <rect x="190" y="668" width="408" height="96" rx="48" fill="url(#pill-gold)"/>
      <circle cx="92" cy="736" r="44" fill="#111" stroke="var(--amber)" stroke-width="5"/>
      <g fill="var(--amber)">
        <path d="M68 724 C70 708 114 708 116 724 L106 728 C104 720 80 720 78 728 Z"/>
        <path d="M76 734 L108 734 L114 758 L70 758 Z"/>
        <circle cx="92" cy="746" r="6" fill="#111"/>
      </g>
    </g>
  </svg>

  <header class="brand">
    <div class="brand-name">Marigold</div>
    <div class="brand-sub">HAIR</div>
    <p class="brand-studio">HOME HAIRDRESSING STUDIO<br>AT FERN RIDGE, WATTLEGROVE</p>
  </header>

  <div class="experience">
    <span class="experience-years">15</span>
    <span class="experience-label">YEARS EXPERIENCE</span>
  </div>

  <h2 class="services-title">SPACIALIZE IN</h2>
  <ul class="services">
    <li><svg viewBox="0 0 20 20"><g fill="none" stroke="#d9b27a" stroke-width="1.6"><circle cx="5" cy="15" r="2.5"/><circle cx="9" cy="17" r="2.5"/><path d="M6.5 13 L17 3 M10 14.8 L15 6"/></g></svg>Foiling</li>
    <li><svg viewBox="0 0 20 20"><g fill="none" stroke="#d9b27a" stroke-width="1.6"><circle cx="5" cy="15" r="2.5"/><circle cx="9" cy="17" r="2.5"/><path d="M6.5 13 L17 3 M10 14.8 L15 6"/></g></svg>Balayage</li>
    <li><svg viewBox="0 0 20 20"><g fill="none" stroke="#d9b27a" stroke-width="1.6"><circle cx="5" cy="15" r="2.5"/><circle cx="9" cy="17" r="2.5"/><path d="M6.5 13 L17 3 M10 14.8 L15 6"/></g></svg>Ombre Colour</li>
    <li><svg viewBox="0 0 20 20"><g fill="none" stroke="#d9b27a" stroke-width="1.6"><circle cx="5" cy="15" r="2.5"/><circle cx="9" cy="17" r="2.5"/><path d="M6.5 13 L17 3 M10 14.8 L15 6"/></g></svg>Tints</li>
    <li><svg viewBox="0 0 20 20"><g fill="none" stroke="#d9b27a" stroke-width="1.6"><circle cx="5" cy="15" r="2.5"/><circle cx="9" cy="17" r="2.5"/><path d="M6.5 13 L17 3 M10 14.8 L15 6"/></g></svg>Style Cutting</li>
    <li><svg viewBox="0 0 20 20"><g fill="none" stroke="#d9b27a" stroke-width="1.6"><circle cx="5" cy="15" r="2.5"/><circle cx="9" cy="17" r="2.5"/><path d="M6.5 13 L17 3 M10 14.8 L15 6"/></g></svg>Blowdrying</li>
  </ul>

  <p class="tagline tagline-accent">more affordable</p>
  <p class="tagline tagline-rest">than a hair salon...</p>

  <div class="contact">
    <p class="contact-lead">sms or call Rosalind</p>
    <p class="contact-number">0412639074</p>
  </div>
</main>
</body>
</html>
```